New Business Card Design Project

We require a business card design for Vexalund, a newly established Indian company.
Our focus is on the development, manufacturing, and export of a diverse array of pharmaceutical products on a global scale. The card should convey a professional appearance, as our primary markets are in Africa, China, and Southeast Asian nations.
We envision a two-sided business card, with the reverse side dedicated to a logo set against a solid color or an elegantly designed pattern. The corners should be rounded. We would appreciate seeing both horizontal and vertical design options. We trust the designer to utilize their expertise in creating this design.

The content for the business card is included in the attached Word file.

Target Market(s)

Our primary markets are in Africa, China, and Southeast Asian, Latin America, Maldives, Sri Lanka

Industry/Entity Type

Pharmaceutical Manufacturing and Export

Contact Information for Business Card

Colors

Designer to choose colors to be used in the design.

Requirements
Must have
• The reverse side of the business card features solely the logo along with the tagline, "Healing for All."
Should not have
• The logo should not exceed two instances, encompassing both the front and back sides of the card.

```html
<!DOCTYPE html>
<html lang="en">
<head>
<meta charset="utf-8">
<title>Vexalund Business Card</title>
<link rel="stylesheet" href="https://fonts.googleapis.com/css2?family=Montserrat:wght@500;700&family=Open+Sans:wght@400;600&display=swap">
<style>
  :root {
    --backdrop: #e6cfb4;
    --card: #202024;
    --blue: #2ea6de;
    --orange: #f0604c;
    --white: #f4f4f4;
  }
  * { margin: 0; padding: 0; box-sizing: border-box; }
  html, body { width: 1200px; height: 711px; overflow: hidden; }
  body {
    background: var(--backdrop);
    position: relative;
    font-family: "Open Sans", sans-serif;
  }
  .card {
    position: absolute;
    top: 205px;
    width: 520px;
    height: 300px;
    background: var(--card);
    border-radius: 22px;
    overflow: hidden;
    box-shadow: 0 18px 40px rgba(60, 35, 15, 0.35);
  }
  .card--back { left: 60px; }
  .card--front { left: 620px; }

  .brand {
    font-family: "Montserrat", sans-serif;
    font-weight: 700;
    color: var(--blue);
    display: flex;
    align-items: center;
    gap: 12px;
    white-space: nowrap;
  }
  .brand__dot {
    width: 16px; height: 16px;
    border-radius: 50%;
    background: var(--orange);
  }

  .card--back .brand-block {
    position: absolute;
    inset: 0;
    display: flex;
    flex-direction: column;
    align-items: center;
    justify-content: center;
  }
  .card--back .brand { font-size: 54px; letter-spacing: 0.5px; }
  .tagline {
    margin-top: 10px;
    font-family: "Montserrat", sans-serif;
    font-weight: 500;
    color: var(--blue);
    font-size: 15px;
    letter-spacing: 0.6px;
    align-self: flex-end;
    margin-right: 80px;
  }

  .card--front .brand {
    position: absolute;
    left: 30px;
    top: 112px;
    font-size: 36px;
  }
  .divider {
    position: absolute;
    left: 262px;
    top: 40px;
    width: 1px;
    height: 180px;
    background: var(--orange);
  }
  .person {
    position: absolute;
    left: 290px;
    top: 44px;
  }
  .person__name {
    font-family: "Montserrat", sans-serif;
    font-weight: 700;
    font-size: 22px;
    color: var(--blue);
    white-space: nowrap;
  }
  .person__name span { color: var(--orange); font-weight: 500; }
  .person__role {
    color: var(--white);
    font-size: 13px;
    margin-top: 2px;
    margin-left: 2px;
  }
  .contacts {
    list-style: none;
    margin-top: 22px;
  }
  .contacts li {
    display: flex;
    align-items: center;
    gap: 10px;
    color: var(--white);
    font-size: 13px;
    line-height: 24px;
    white-space: nowrap;
  }
  .contacts svg { width: 14px; height: 14px; flex: none; }

  .address-band {
    position: absolute;
    left: 0; right: 0; bottom: 0;
    height: 40px;
    background: var(--blue);
    display: flex;
    align-items: center;
    padding-left: 30px;
    color: var(--white);
    font-size: 14px;
    letter-spacing: 0.3px;
    white-space: nowrap;
  }
  .address-band::after {
    content: "";
    position: absolute;
    right: 0; top: 0; bottom: 0;
    width: 70px;
    background: var(--orange);
  }
</style>
</head>
<body>

<section class="card card--back" aria-label="Card back">
  <div class="brand-block">
    <div class="brand"><span class="brand__dot"></span>Vexalund</div>
    <p class="tagline">Healing for All.</p>
  </div>
</section>

<section class="card card--front" aria-label="Card front">
  <div class="brand"><span class="brand__dot"></span>Vexalund</div>
  <div class="divider"></div>

  <div class="person">
    <p class="person__name">Rohan <span>K. Varma</span></p>
    <p class="person__role">CEO</p>
    <ul class="contacts">
      <li>
        <svg viewBox="0 0 14 14" aria-hidden="true"><rect x="1.5" y="1.5" width="11" height="11" fill="none" stroke="#f0604c" stroke-width="1.6"/></svg>
        +91 98765 43210
      </li>
      <li>
        <svg viewBox="0 0 14 14" aria-hidden="true"><circle cx="7" cy="7" r="6" fill="#2ea6de"/><path d="M1 7h12M7 1c-3 3-3 9 0 12M7 1c3 3 3 9 0 12" stroke="#202024" stroke-width="0.9" fill="none"/></svg>
        www.vexalund.com
      </li>
      <li>
        <svg viewBox="0 0 14 14" aria-hidden="true"><rect x="1" y="3" width="12" height="9" rx="1" fill="#f0604c"/><path d="M1.5 3.5 7 8l5.5-4.5" stroke="#202024" stroke-width="1.1" fill="none"/></svg>
        rvarma@vexalund.com
      </li>
    </ul>
  </div>

  <div class="address-band">12, Neelkanth Nagar, Nashik, 422001, India</div>
</section>

</body>
</html>
```